Business Card Design

We are a company that provides stump grinding services for residential and commercial clients. Looking for a simple business card design that may have some type of graphic on the card that will tie in with the Tamsen name(Grizzly Bear, Paw Print, etc) . Possibly some foliage wrapping around part of the card? Would like to have a simple design that stands out because it is unique. We are working on getting the website set up and there is a simple graphic on the top of the page that came to mind when I mentioned the leaves.

Industry/Entity Type

Business

Contact Information for Business Card

Tamsen Stump Grinding 303-257-4788KodiakStumps.Com

Font styles to use
Serif

Requirements
Must have
• Business name
• Website Address
• Phone Number
Nice to have
• Graphics that would be associated with a Tamsen bear.
Should not have
• Nothing frilly

```html
<!DOCTYPE html>
<html lang="en">
<head>
<meta charset="utf-8">
<title>Tamsen Stump Grinding – Business Card</title>
<link rel="stylesheet" href="https://fonts.googleapis.com/css2?family=Cinzel:wght@400&family=Open+Sans:wght@400&display=swap">
<style>
  :root {
    --backdrop-top: #8c8c8c;
    --backdrop-bottom: #6a6a6a;
    --card-light: #f3f3f3;
    --card-dark: #000000;
    --ink: #111111;
    --ink-soft: #8e8e8e;
    --ink-faint: #1c1c1c;
    --paper: #ffffff;
  }
  * { margin: 0; padding: 0; box-sizing: border-box; }
  html, body { width: 1200px; height: 900px; overflow: hidden; }
  body {
    position: relative;
    background: linear-gradient(180deg, var(--backdrop-top), var(--backdrop-bottom));
    font-family: "Cinzel", serif;
  }
  .card {
    position: absolute;
    top: 185px;
    width: 302px;
    height: 490px;
    border-radius: 11px;
    overflow: hidden;
    text-align: center;
  }
  .card--front { left: 299px; background: var(--card-light); }
  .card--back  { left: 645px; width: 305px; background: var(--card-dark); }

  .brand-mark {
    position: absolute;
    left: 0; right: 0;
    font-weight: 400;
    letter-spacing: 2px;
  }
  .card--front .brand-mark {
    top: 62px;
    font-size: 30px;
    color: var(--ink);
  }
  .card--back .brand-mark {
    top: 240px;
    font-size: 60px;
    color: var(--ink-faint);
    letter-spacing: 3px;
  }

  .business-name {
    position: absolute;
    left: 0; right: 0;
    font-weight: 400;
    line-height: 1;
  }
  .card--front .business-name { top: 136px; }
  .card--back  .business-name { top: 375px; }
  .business-name__main {
    display: block;
    font-size: 28px;
    letter-spacing: 0.5px;
  }
  .business-name__sub {
    display: block;
    margin-top: 12px;
    font-size: 22px;
    letter-spacing: 9px;
    padding-left: 9px;
    color: var(--ink-soft);
  }
  .card--front .business-name__main { color: var(--ink); }
  .card--back  .business-name__main { color: var(--paper); }

  .contact {
    position: absolute;
    left: 0; right: 0;
    top: 394px;
    list-style: none;
    font-family: "Open Sans", sans-serif;
    font-size: 13px;
    line-height: 20px;
    color: var(--ink);
  }
  .contact__item { display: flex; justify-content: center; align-items: center; gap: 6px; }
  .contact__icon { width: 11px; height: 11px; }
</style>
</head>
<body>
  <section class="card card--front">
    <div class="brand-mark">TAMSEN</div>
    <h1 class="business-name">
      <span class="business-name__main">TAMSEN STUMP</span>
      <span class="business-name__sub">GRINDING</span>
    </h1>
    <ul class="contact">
      <li class="contact__item">
        <svg class="contact__icon" viewBox="0 0 12 12" aria-hidden="true">
          <path d="M1 4.5 Q6 0.5 11 4.5 L9.5 6 L8 4.8 L4 4.8 L2.5 6 Z" fill="#111"/>
          <rect x="2.5" y="6" width="7" height="4.5" rx="1" fill="#111"/>
        </svg>
        <span>303-555-0146</span>
      </li>
      <li class="contact__item">
        <svg class="contact__icon" viewBox="0 0 12 12" aria-hidden="true">
          <g fill="none" stroke="#111" stroke-width="1.2">
            <rect x="0.8" y="5.2" width="6" height="3.2" rx="1.6" transform="rotate(-45 3.8 6.8)"/>
            <rect x="5.2" y="3.6" width="6" height="3.2" rx="1.6" transform="rotate(-45 8.2 5.2)"/>
          </g>
        </svg>
        <span>TamsenStumps.Com</span>
      </li>
    </ul>
  </section>

  <section class="card card--back">
    <div class="brand-mark" aria-hidden="true">TAMSEN</div>
    <h2 class="business-name">
      <span class="business-name__main">TAMSEN STUMP</span>
      <span class="business-name__sub">GRINDING</span>
    </h2>
  </section>
</body>
</html>
```